Web design project for exciting Australian start-up

Background
We are looking for a creative and talented web design artist to work alongside our market leading web developer.
• You will be required to create a modern and clean design theme for our website, incorporating selected rustic colour scheme elements for our exciting Australian start-up to operate within the coffee industry.
reoccurring work to be expected to flow to the successful designer.
Requirements
• c. 5 - 10 page website
• Landing page
• Log in/ out
• 404 template
• Typography is emphasised
• Please use either a) typemarrow.com, b) free web fonts, c) brindle fonts
• All design elements in vector format
• Preferably with icons for each header title(i.e. about us, how it works etc) but designer have free reign over how the site looks, so might not be applicable
• All pages to be responsive
• Down to eSlab resolution

High level visual design brief attached - additional pages to be worked from base design.

Design inspiration
• We would like to use design elements from the following sources:
http://www.zandrix.com/halcyon/ (Functionality)
Colour scheme refer to logo and complementary style guide

```html
<!DOCTYPE html>
<html lang="en">
<head>
<meta charset="utf-8">
<title>Roast Hollow – Marketplace</title>
<link rel="stylesheet" href="https://fonts.googleapis.com/css2?family=Oxygen:wght@400;700&family=Roboto+Condensed:wght@700&family=Arimo:wght@400;700&display=swap">
<style>
  :root {
    --charcoal: #4a4b49;
    --charcoal-dark: #3a3b39;
    --orange: #e09a4a;
    --orange-bright: #f07f0f;
    --ink: #1e1e1e;
    --white: #ffffff;
    --paper: #ffffff;
    --field-border: #9a9a9a;
  }
  * { box-sizing: border-box; margin: 0; padding: 0; }
  html, body { width: 1200px; height: 787px; overflow: hidden; background: var(--paper); }
  body { position: relative; font-family: "Arimo", Arial, sans-serif; color: var(--ink); }

  .brand {
    position: absolute; left: 172px; top: 17px; height: 91px;
    display: flex; align-items: center; gap: 12px;
  }
  .brand-mark {
    width: 80px; height: 80px; border-radius: 50%;
    background: var(--orange);
  }
  .brand-name {
    font-family: "Roboto Condensed", "Arial Narrow", sans-serif; font-weight: 700;
    font-size: 34px; letter-spacing: 1px; color: var(--ink);
  }

  .account-nav { position: absolute; top: 45px; left: 669px; display: flex; gap: 9px; }
  .account-nav a {
    display: flex; align-items: center; justify-content: center; gap: 9px;
    height: 36px; color: var(--white); text-decoration: none;
    font-size: 15.5px; background: var(--charcoal);
  }
  .account-nav .my-account { width: 118px; background: linear-gradient(#3f403e, #555653); }
  .account-nav .logged-in { width: 118px; }
  .account-nav .log-out { width: 106px; background: var(--orange); }
  .lock { width: 11px; height: 12px; }

  .hero {
    position: absolute; left: 172px; top: 122px; width: 856px; height: 423px;
    border-top: 1px solid #777;
    background:
      radial-gradient(ellipse 260px 200px at 640px 220px, #cfc9c2 0%, #bdb4aa 35%, rgba(120,80,50,0) 70%),
      radial-gradient(ellipse 200px 160px at 110px 140px, #a88a62 0%, rgba(120,90,60,0) 75%),
      linear-gradient(160deg, #4a2a18 0%, #5c3520 40%, #3b2114 70%, #6a4a33 100%);
  }
  .hero-title {
    position: absolute; left: 66px; top: 255px;
    font-family: "Oxygen", sans-serif; font-size: 40px; line-height: 44px;
    color: var(--white); font-weight: 400;
  }
  .tender-button {
    position: absolute; left: 67px; top: 311px; width: 205px; height: 43px;
    display: flex; border: 1px solid #f0c58f; text-decoration: none;
  }
  .tender-button .chevron {
    width: 44px; background: var(--charcoal); color: var(--white);
    display: flex; align-items: center; justify-content: center;
  }
  .tender-button .label {
    flex: 1; background: var(--orange); color: var(--white);
    font-family: "Oxygen", sans-serif; font-size: 16px; letter-spacing: .3px;
    display: flex; align-items: center; justify-content: center;
  }

  .accent-band { position: absolute; left: 172px; top: 545px; width: 856px; height: 5px; background: var(--orange); }

  .site-footer {
    position: absolute; left: 172px; top: 550px; width: 856px; height: 166px;
    background: var(--charcoal); color: var(--white);
    box-shadow: 0 10px 12px -8px rgba(0,0,0,.35);
  }
  .footer-col { position: absolute; top: 16px; }
  .footer-col h2 { font-family: "Oxygen", sans-serif; font-weight: 400; font-size: 15px; line-height: 20px; height: 20px; }
  .footer-col ul { list-style: none; margin-top: 30px; }
  .footer-col li { font-size: 10.5px; line-height: 19px; }
  .col-help { left: 18px; }
  .col-who { left: 222px; }
  .col-join { left: 412px; }
  .col-news { left: 569px; width: 268px; }
  .email-field {
    margin-top: 26px; width: 266px; height: 30px; border: 1px solid var(--field-border);
    background: var(--white); color: #b5b5b5; font-size: 11.5px; padding: 7px 14px;
    box-shadow: inset 0 2px 3px rgba(0,0,0,.25);
  }
  .news-actions { display: flex; gap: 17px; margin-top: 17px; }
  .news-actions a {
    display: flex; align-items: center; gap: 8px; justify-content: center;
    height: 30px; width: 124px; color: var(--white); text-decoration: none;
    font-weight: 700; font-size: 12.5px;
  }
  .subscribe { background: var(--orange-bright); }
  .unsubscribe { background: var(--charcoal-dark); }
  .envelope { width: 20px; height: 14px; }

  .copyright { position: absolute; left: 0; width: 1243px; top: 745px; text-align: center; font-size: 10.5px; }
  .page-code { position: absolute; left: 1054px; top: 747px; font-size: 10px; }
</style>
</head>
<body>
  <header>
    <div class="brand">
      <span class="brand-mark"></span>
      <span class="brand-name">ROAST HOLLOW</span>
    </div>
    <nav class="account-nav">
      <a class="my-account" href="#">My account</a>
      <a class="logged-in" href="#">
        <svg class="lock" viewBox="0 0 11 12"><path d="M3 5V3.5a2.5 2.5 0 0 1 5 0V5" fill="none" stroke="#fff" stroke-width="1.6"/><rect x="1" y="5" width="9" height="7" fill="#fff"/></svg>
        Logged in
      </a>
      <a class="log-out" href="#">
        <svg class="lock" viewBox="0 0 11 12"><path d="M3 5V3.5a2.5 2.5 0 0 1 5 0V5" fill="none" stroke="#fff" stroke-width="1.6"/><rect x="1" y="5" width="9" height="7" fill="#fff"/></svg>
        Log out
      </a>
    </nav>
  </header>

  <main>
    <section class="hero" role="img" aria-label="Photograph of a white espresso cup with cinnamon sticks and star anise on a saucer, surrounded by spilled coffee beans and a burlap sack on a wooden table">
      <h1 class="hero-title">Marketplace</h1>
      <a class="tender-button" href="#">
        <span class="chevron"><svg width="10" height="16" viewBox="0 0 10 16"><path d="M2 2l6 6-6 6" fill="none" stroke="#fff" stroke-width="3"/></svg></span>
        <span class="label">START A TENDER</span>
      </a>
    </section>
    <div class="accent-band"></div>
  </main>

  <footer class="site-footer">
    <div class="footer-col col-help">
      <h2>Helpful info</h2>
      <ul><li>About us</li><li>Media enquiries</li><li>Terms &amp; conditions</li><li>Privacy policy</li></ul>
    </div>
    <div class="footer-col col-who">
      <h2>Who we are</h2>
      <ul><li>How it works</li><li>FAQ</li><li>Contact us</li></ul>
    </div>
    <div class="footer-col col-join">
      <h2>Join us on</h2>
      <ul><li>Friendloop</li><li>Chirpline</li><li>Workgrid</li><li>Clipstream</li></ul>
    </div>
    <div class="footer-col col-news">
      <h2>Subscribe to our Newsletter</h2>
      <div class="email-field">Enter Your Email...</div>
      <div class="news-actions">
        <a class="subscribe" href="#">
          <svg class="envelope" viewBox="0 0 20 14"><rect x="1" y="1" width="18" height="12" fill="none" stroke="#fff" stroke-width="1.6"/><path d="M1 1l9 7 9-7M1 13l7-6M19 13l-7-6" fill="none" stroke="#fff" stroke-width="1.4"/></svg>
          Subscribe
        </a>
        <a class="unsubscribe" href="#">
          <svg class="envelope" viewBox="0 0 20 14"><rect x="1" y="1" width="18" height="12" fill="none" stroke="#fff" stroke-width="1.6"/><path d="M1 1l9 7 9-7M1 13l7-6M19 13l-7-6" fill="none" stroke="#fff" stroke-width="1.4"/></svg>
          Unsubscribe
        </a>
      </div>
    </div>
  </footer>

  <p class="copyright">Copyright © 2014 Roast Hollow</p>
  <p class="page-code">C7</p>
</body>
</html>
```